Brochure required

Looking at getting business brochure designed for my solar sales company. i will require a range of products to be listed on the brochure I require a simple/ elegent / professional looking brochure.

I am happy to provide designer with all the required information that must go into the brochure. otherwise please visit www.quillebartow.com.au and view the products which i would like to allocate into the brochure aswell as our company logo and a little about me section

```html
<!DOCTYPE html>
<html lang="en">
<head>
<meta charset="utf-8">
<title>Quillebartow – Products We Offer Brochure</title>
<link rel="stylesheet" href="https://fonts.googleapis.com/css2?family=Open+Sans:wght@400;600;700;800&display=swap">
<style>
  :root {
    --backdrop: #e6e6e8;
    --page-white: #ffffff;
    --page-grey: #c8c8c9;
    --heading-blue: #1e8ec4;
    --accent-green: #16a05a;
    --rule-green: #1a8a4f;
    --body-text: #4a4a4a;
    --body-dark: #1f1f1f;
    --sky-light: #7fb6e8;
    --sky-deep: #0a2a8a;
    --panel-blue: #2b4fb0;
    --grass: #3c9a2a;
  }
  * { box-sizing: border-box; margin: 0; padding: 0; }
  html, body {
    width: 1200px; height: 840px; overflow: hidden;
    background: var(--backdrop);
    font-family: "Open Sans", sans-serif;
  }
  .spread {
    position: absolute; left: 120px; top: 70px;
    width: 960px; height: 700px;
    display: flex;
    box-shadow: 0 18px 40px rgba(0,0,0,0.18);
  }
  .page { position: relative; width: 480px; height: 700px; overflow: hidden; }
  .page--left { background: var(--page-white); }
  .page--right { background: var(--page-grey); }

  .section-title {
    position: absolute; left: 36px; top: 44px;
    color: var(--heading-blue); font-weight: 800; font-size: 21px;
    letter-spacing: 0.2px;
  }
  .product-heading {
    color: var(--accent-green); font-weight: 700; font-size: 13px;
  }
  .left-heading { position: absolute; left: 36px; top: 76px; }
  .rule { position: absolute; }
  .rule--left { left: 150px; top: 80px; width: 330px; height: 12px; }
  .rule--right { left: 0; top: 36px; width: 480px; height: 12px; }

  .body-copy {
    font-size: 9.6px; line-height: 1.5; color: var(--body-text);
  }
  .left-copy { position: absolute; left: 36px; top: 106px; width: 410px; }
  .left-copy p + p { margin-top: 18px; }

  .photo { position: absolute; }
  .photo--field {
    left: 0; top: 400px; width: 480px; height: 262px;
    background: linear-gradient(180deg, var(--sky-light) 0%, #cfe3f6 38%, var(--panel-blue) 58%, #2f6fc2 68%, var(--grass) 78%, #5fb33a 100%);
  }
  .photo--tracker {
    left: 0; top: 300px; width: 480px; height: 336px;
    background: linear-gradient(180deg, var(--sky-deep) 0%, #1a3fa8 55%, #2b5fc4 72%, var(--grass) 86%, #2f8a20 100%);
  }

  .right-block { position: absolute; left: 36px; width: 410px; }
  .right-block--panels { top: 66px; }
  .right-block--batteries { top: 212px; }
  .right-block .body-copy { color: var(--body-dark); margin-top: 8px; text-align: justify; }

  .web-address {
    position: absolute; right: 34px; bottom: 22px;
    font-size: 15px; font-weight: 700; color: var(--body-dark);
  }
  .web-address .brand { color: var(--accent-green); }
</style>
</head>
<body>
  <main class="spread">
    <section class="page page--left">
      <h1 class="section-title">PRODUCTS WE OFFER</h1>
      <h2 class="product-heading left-heading">Solar Inverters</h2>
      <svg class="rule rule--left" viewBox="0 0 330 12" aria-hidden="true">
        <circle cx="5" cy="6" r="4" fill="var(--rule-green)"/>
        <line x1="5" y1="6" x2="330" y2="6" stroke="var(--rule-green)" stroke-width="1.6"/>
      </svg>
      <div class="body-copy left-copy">
        <p>The inverter is the heart of your solar power system. Its primary functions are to convert the DC power from the panels into AC power for your home and to select the most productive operating voltage for the panels. Inverters come in a wide range of types, quality and sizes. The most common types of inverters are string inverters, which are mounted on your wall and connect to all the panels in your system.</p>
        <p>Another popular type is micro inverters, which are small inverters that sit under each panel. These inverters manage each panel individually, resulting in better yields, particularly on challenging roofs or systems subject to shading. Better quality inverters have better features, they come with longer warranties, generate more power and are far more reliable. Better inverter manufacturers are also starting to introduce different connectivity options, online management portals, external devices for consumption monitoring, and are now starting to include battery connectivity (hybrid inverters). We have one of Australia's largest selections of inverters and can recommend the perfect option for your solar project.</p>
      </div>
      <div class="photo photo--field" role="img" aria-label="Photo of rows of solar panel arrays on green grass under a blue sky with white clouds"></div>
    </section>

    <section class="page page--right">
      <svg class="rule rule--right" viewBox="0 0 480 12" aria-hidden="true">
        <line x1="0" y1="6" x2="440" y2="6" stroke="var(--rule-green)" stroke-width="1.6"/>
        <circle cx="440" cy="6" r="4" fill="var(--rule-green)"/>
      </svg>
      <div class="right-block right-block--panels">
        <h2 class="product-heading">Solar Panels</h2>
        <p class="body-copy">Quillebartow has partnered with the most reputable solar PV manufacturers in the world to offer you the best solar panels on the market. We have selected high-end PV modules with the best track records to ensure we supply top-quality products to our customers. Whether you are looking to buy solar panels for residential or commercial use, look no further. Quillebartow provides superior solar panels for home and business purposes, sourced from trusted tier-1 manufacturers, as well as premium-brand solar power inverters.</p>
      </div>
      <div class="right-block right-block--batteries">
        <h2 class="product-heading">Solar Batteries</h2>
        <p class="body-copy">Energy storage systems are now a reality, and homes like yours is where it begins. In the next few years, we will see a fundamental shift in the way all energy users meet their energy requirements and how utility providers integrate with storage systems. For home owners, they can benefit right now from energy storage in a variety of ways.</p>
      </div>
      <div class="photo photo--tracker" role="img" aria-label="Photo of a single solar tracker panel on a green hill against a deep blue sky"></div>
      <p class="web-address">www.<span class="brand">quillebartow</span>.com.au</p>
    </section>
  </main>
</body>
</html>
```